Web Design For Marlow Pool Service

We are working with a company that wants a website for their pool service. Some sites to use for content/competitors and inspiration:
https://sacramento.brightwaterpoolco.example/builder/newbuild/repair/ppc
https://hollowbrookpoolcareplus.example/
https://lakemontpoolservice.example/
https://www.dravenspoolresurfacing.example/pool-renovation-ga/
Thank you for taking the time to consider designing a website for us. We are web developers based in Stockton, CA, USA. Most of our projects go through the same process. Understanding this process may help you win a project with us. We custom-code all of our websites in-house. We don’t have any requirements as to what tools you use for your design, but we prefer Figma files. For any design that we label as four-stars, we send it to the client for review. The client picks the final design they want us to use. Once we complete this process, we will continue to show additional clients all the four-star sites and purchase them later. Your designs will have multiple chances to sell. For better chances of success, we ask that you follow these guidelines.
IMAGES:
If you use any images or icons in the design, we ask that you have a link to the asset so we can purchase the image/icon. Most of the designs we submit do not have the customer’s images on them unless they have some great images. Be creative; show us the feeling you are trying to portray with your image choices. Use any royalty-free site you choose. We subscribe to Adobe and mainly use their images, but we can purchase images outside of Adobe. PLEASE NOTE: we will not submit designs to clients with watermarks on the images.
FONTS:
We ask that you identify the fonts used in the design. This can be done in a message if you want. We typically use Google Fonts and Adobe Fonts.
CONTENT:
We're always open to different content and ideas. We often submit designs with stock images so the client can see our vision. We typically take pictures after the website launch to use their images with our vision. Lorem Ipsum is fine for paragraphs, but we ask that you write the headers in correct English. We want to be able to show the vision and identify the sections of the website.
INSPIRATION:
We typically add a couple of links in the brief of websites we like to help you get started in your design.
REVISIONS:
We do not often ask for revisions of the designs unless we see something in the design that may not appeal to the client. If there are slight changes that we want to make, we do that in the development process.
FEEDBACK:
We rarely give feedback on designs during the design process. We are working on many website projects and do not have the time to provide feedback. We usually respond if your request is well thought out and asks specific questions, but a note asking “feedback, please” usually goes unanswered.
Number of Pages Required
1 page
Look and feel
Each slider illustrates characteristics of the customer's brand and the style your logo design should communicate.

```html
<!DOCTYPE html>
<html lang="en">
<head>
<meta charset="utf-8">
<title>Marlow Pool Service</title>
<link href="https://fonts.googleapis.com/css2?family=Cinzel:wght@500;600&family=Roboto:wght@400;500;700&display=swap" rel="stylesheet">
<style>
:root{
  --blue:#0a5eb5;
  --blue-dark:#0550a3;
  --sky:#3fa9e8;
  --pale:#cfe4f3;
  --ink:#222;
  --text:#707070;
  --white:#fff;
}
*{box-sizing:border-box;margin:0;padding:0}
html,body{width:1200px;height:3294px;overflow:hidden}
body{position:relative;background:var(--white);font-family:"Roboto",Arial,sans-serif;color:var(--ink)}
.abs{position:absolute}
.photo{position:absolute}
.btn{position:absolute;display:flex;align-items:center;justify-content:center;border-radius:24px;font-weight:500;font-size:15px;text-transform:uppercase;background:var(--blue);color:var(--white)}
.btn.outline{background:var(--white);color:var(--blue);border:2px solid var(--blue)}
.heading{font-family:"Cinzel",Georgia,serif;font-weight:500;color:var(--ink);font-size:47px;letter-spacing:1px}
.heading .accent{color:var(--blue)}

/* header */
.site-header{left:0;top:0;width:1200px;height:80px;background:var(--white)}
.brand{left:143px;top:18px;font-family:"Cinzel",Georgia,serif;font-weight:600;font-size:24px;color:var(--sky);letter-spacing:1px;line-height:1}
.brand small{display:block;font-size:17px;font-weight:600;letter-spacing:3px;margin-top:4px;padding-left:36px}
.main-nav{left:471px;top:33px;display:flex;gap:26px;font-size:13px;font-weight:500;text-transform:uppercase;color:var(--ink)}
.call-btn{left:879px;top:22px;width:176px;height:38px;background:var(--blue);color:var(--white);font-size:14px;font-weight:500;display:flex;align-items:center;gap:10px;padding-left:12px}
.call-btn .ico{width:26px;height:26px;border-radius:50%;background:var(--white);display:flex;align-items:center;justify-content:center}

/* hero */
.hero{left:0;top:80px;width:1200px;height:540px;background:linear-gradient(180deg,#6f8f5f 0%,#a9b9a1 25%,#4d8bb8 55%,#1f6aa8 80%,#2f86c6 100%)}
.hero-circle{left:132px;top:134px;width:384px;height:384px;border-radius:50%;background:rgba(18,88,150,.82)}
.hero-title{left:132px;top:240px;width:384px;text-align:center;font-family:"Cinzel",Georgia,serif;font-weight:500;font-size:46px;line-height:46px;color:var(--white)}
.hero .btn{left:237px;top:400px;width:170px;height:40px}
.slider-dots{left:1138px;top:405px;display:flex;flex-direction:column;gap:10px}
.slider-dots span{width:8px;height:8px;border-radius:50%;background:var(--white)}
.slider-dots span.on{width:10px;height:10px;background:none;border:2px solid var(--white)}

/* about */
.about-text{left:573px;top:803px;width:481px;font-size:13.5px;line-height:25.6px;color:var(--text);text-align:justify}

/* services */
.card{position:absolute;top:1361px;width:290px;height:375px;background:var(--blue);color:var(--white);text-align:center}
.card h3{font-size:16px;font-weight:700;text-transform:uppercase;margin-bottom:8px}
.card p{font-size:14px;line-height:22px;padding:0 22px}
.card .btn{position:static;display:inline-flex;margin-top:12px;width:107px;height:30px;font-size:12px;background:var(--blue-dark);box-shadow:0 0 0 1px rgba(255,255,255,.15)}
.card .body{position:absolute;left:0;width:100%}
.card .icon{position:absolute;left:118px;width:54px;height:54px;border-radius:50%;background:var(--white);display:flex;align-items:center;justify-content:center}
.dots{left:576px;top:1775px;display:flex;gap:12px}
.dots span{width:8px;height:8px;border-radius:50%;background:#ccc}
.dots span.on{background:var(--blue)}

/* cta */
.cta-band{left:0;top:1829px;width:1200px;height:384px;background:linear-gradient(90deg,#5aa7dc,#7cc0ea 50%,#5ba9de)}
.cta-box{left:407px;top:1893px;width:386px;height:256px;background:var(--white);text-align:center}
.cta-box h2{margin-top:26px;font-size:46px;line-height:48px;font-weight:700;color:var(--ink)}
.cta-phone{margin-top:12px;display:flex;justify-content:center;align-items:center;gap:12px;font-size:24px;font-weight:500;color:var(--blue)}
.cta-box .btn{left:110px;top:184px;width:170px;height:40px}

/* footer */
.footer-nav{left:435px;top:3105px;display:flex;gap:34px;font-size:17px;font-weight:500;color:var(--white);text-transform:uppercase}
.footer-rule{left:388px;top:3148px;width:667px;height:1px;background:rgba(255,255,255,.25)}
.copyright{left:435px;top:3167px;font-size:13px;color:var(--white)}
.social{left:435px;top:3207px;display:flex;gap:14px}
.social span{width:30px;height:30px;border-radius:50%;background:var(--white)}
</style>
</head>
<body>

<header class="abs site-header">
  <div class="abs brand">Marlow<small>Pool Service</small></div>
  <nav class="abs main-nav"><span>Home</span><span>About Us</span><span>Services</span><span>News</span><span>Contact Us</span></nav>
  <div class="abs call-btn"><span class="ico"><svg width="14" height="14" viewBox="0 0 24 24"><path fill="#0a5eb5" d="M6.6 10.8a15 15 0 0 0 6.6 6.6l2.2-2.2c.3-.3.7-.4 1-.2 1.1.4 2.3.6 3.6.6.6 0 1 .4 1 1V20c0 .6-.4 1-1 1A17 17 0 0 1 3 4c0-.6.4-1 1-1h3.5c.6 0 1 .4 1 1 0 1.3.2 2.5.6 3.6.1.3 0 .7-.2 1z"/></svg></span>+1 555 010 2040</div>
</header>

<section class="abs hero">
  <div class="photo" style="inset:0" role="img" aria-label="Modern villa with a blue infinity pool, palm trees and flowering shrubs"></div>
  <div class="abs hero-circle"></div>
  <h1 class="abs hero-title">Bring Your<br>Dream Pool<br>To Life</h1>
  <div class="btn">Request a Quote</div>
  <div class="abs slider-dots"><span class="on"></span><span></span><span></span></div>
</section>
<svg class="abs" style="left:0;top:550px" width="1200" height="75" viewBox="0 0 1200 75" preserveAspectRatio="none">
  <path d="M0 25 C150 10 260 45 420 30 S700 5 860 22 S1080 40 1200 12 V75 H0Z" fill="var(--blue)"/>
  <path d="M0 58 C180 42 320 68 520 55 S820 38 1000 52 S1140 60 1200 48 V75 H0Z" fill="var(--white)"/>
</svg>

<section aria-label="Who we are">
  <div class="photo" style="left:166px;top:692px;width:300px;height:300px;border-radius:50%;background:linear-gradient(160deg,#9aa3a6,#6f8eb0 60%,#2f6fb8)" role="img" aria-label="Technicians tiling a pool edge"></div>
  <div class="photo" style="left:373px;top:711px;width:162px;height:162px;border-radius:50%;border:6px solid var(--white);background:linear-gradient(180deg,#3ca7e0,#1c6fbf)" role="img" aria-label="Pool cleaning hose and tools on the pool floor"></div>
  <div class="photo" style="left:150px;top:893px;width:197px;height:197px;border-radius:50%;border:6px solid var(--white);background:linear-gradient(180deg,#8a9a84,#3ea4d4 45%,#1f7fc0)" role="img" aria-label="Pool with a cleaning hose in the water"></div>
  <h2 class="abs heading" style="left:573px;top:728px"><span class="accent">Who</span> We Are</h2>
  <p class="abs about-text">Sed ut perspiciatis unde omnis iste natus error sit voluptatem accusantium doloremque laudantium, totam rem aperiam, eaque ipsa quae ab illo inventore veritatis et quasi architecto beatae vitae dicta sunt explicabo. Nemo enim ipsam voluptatem quia voluptas sit aspernatur aut odit aut fugit, sed quia consequuntur magni dolores eos qui ratione voluptatem sequi nesciunt. Neque porro quisquam est, qui dolorem ipsum quia dolor sit amet, consecteturSed ut perspiciatis unde omnis iste natus error sit voluptatem accusantium doloremque laudantium, totam rem aperiam, eaque ipsa</p>
  <div class="btn" style="left:573px;top:1024px;width:130px;height:39px">Read More</div>
  <div class="btn outline" style="left:709px;top:1024px;width:170px;height:39px">Request a Quote</div>
</section>

<svg class="abs" style="left:0;top:1140px" width="1200" height="70" viewBox="0 0 1200 70" preserveAspectRatio="none">
  <path d="M0 30 C160 15 300 55 460 35 S720 5 880 28 S1080 45 1200 22 V42 C1080 62 960 48 840 50 S560 62 420 55 S160 48 0 60Z" fill="var(--pale)"/>
</svg>

<section aria-label="Our services">
  <h2 class="abs heading" style="left:0;width:1200px;text-align:center;top:1275px"><span class="accent">Our</span> Services</h2>

  <article class="card" style="left:145px">
    <div class="photo" style="left:0;top:0;width:290px;height:168px;background:linear-gradient(160deg,#4d7a4a,#2e6fb0 55%,#b86a3e)" role="img" aria-label="Backyard pool beside a wooden deck"></div>
    <div class="icon" style="top:141px"><svg width="26" height="20" viewBox="0 0 26 20"><path d="M2 12c3-2 5 2 8 0s5 2 8 0 5 2 6 0M2 17c3-2 5 2 8 0s5 2 8 0 5 2 6 0" stroke="#0a5eb5" stroke-width="2" fill="none"/></svg></div>
    <div class="body" style="top:220px"><h3>Swimming Pool Services</h3><p>Sed ut perspiciatis unde omnis iste natus error sit voluptatem accusantium doloremque laudantium,</p><span class="btn">Read More</span></div>
  </article>

  <article class="card" style="left:455px">
    <div class="body" style="top:24px"><h3>Pool Cleaning Service</h3><p>Sed ut perspiciatis unde omnis iste natus error sit voluptatem accusantium doloremque laudantium,</p><span class="btn">Read More</span></div>
    <div class="photo" style="left:0;top:207px;width:290px;height:168px;background:linear-gradient(135deg,#1a6fd0,#2ca0e8 55%,#d7a27a)" role="img" aria-label="Aerial view of a pool being vacuumed"></div>
    <div class="icon" style="top:180px"><svg width="26" height="20" viewBox="0 0 26 20"><rect x="3" y="6" width="20" height="10" rx="2" stroke="#0a5eb5" stroke-width="2" fill="none"/><path d="M8 6V2M18 6V2" stroke="#0a5eb5" stroke-width="2"/></svg></div>
  </article>

  <article class="card" style="left:765px">
    <div class="photo" style="left:0;top:0;width:290px;height:168px;background:linear-gradient(150deg,#233a5e,#3d6fae 50%,#6aa6d4)" role="img" aria-label="Technician repairing pool tiles"></div>
    <div class="icon" style="top:141px"><svg width="22" height="22" viewBox="0 0 22 22"><circle cx="11" cy="11" r="8" stroke="#0a5eb5" stroke-width="2" fill="none"/><path d="M7 11h8M11 7v8" stroke="#0a5eb5" stroke-width="2"/></svg></div>
    <div class="body" style="top:220px"><h3>Swimming Pool Repair</h3><p>Sed ut perspiciatis unde omnis iste natus error sit voluptatem accusantium doloremque laudantium,</p><span class="btn">Read More</span></div>
  </article>

  <div class="abs dots"><span class="on"></span><span></span><span></span></div>
</section>

<section class="abs cta-band" role="img" aria-label="Empty tiled pool with a worker kneeling on the floor"></section>
<div class="abs cta-box">
  <h2>MARLOW POOL<br>SERVICE</h2>
  <div class="cta-phone"><svg width="28" height="28" viewBox="0 0 24 24"><circle cx="12" cy="12" r="12" fill="#0a5eb5"/><path fill="#fff" d="M8.5 11a8 8 0 0 0 4.5 4.5l1.4-1.4c.2-.2.5-.2.7-.1.7.2 1.4.4 2.2.4.3 0 .6.3.6.6v2.2c0 .4-.3.6-.6.6A10.5 10.5 0 0 1 6.2 6.8c0-.3.3-.6.6-.6H9c.4 0 .6.3.6.6 0 .8.1 1.5.4 2.2 0 .3 0 .5-.2.7z"/></svg>+1 555 010 2040</div>
  <div class="btn">Request a Quote</div>
</div>

<section aria-label="Our portfolio">
  <h2 class="abs heading" style="left:0;width:1200px;text-align:center;top:2308px"><span class="accent">Our</span> Portfolio</h2>
  <div class="photo" style="left:145px;top:2403px;width:525px;height:434px;background:linear-gradient(180deg,#8a7d6e,#6b6a5e 55%,#4fb0e0 80%,#2f90cf)" role="img" aria-label="Worker skimming a pool in front of a stone wall"></div>
  <div class="photo" style="left:675px;top:2403px;width:188px;height:215px;background:linear-gradient(180deg,#3a6fb0,#3f7b3e 40%,#47c3e6 70%,#2a9fd8)" role="img" aria-label="Outdoor pool surrounded by trees"></div>
  <div class="photo" style="left:867px;top:2403px;width:188px;height:215px;background:linear-gradient(135deg,#2e8fd6,#56b8ea 60%,#b89a78)" role="img" aria-label="Pool ladder rails in clear water"></div>
  <div class="photo" style="left:675px;top:2623px;width:380px;height:214px;background:linear-gradient(180deg,#eef0ef,#cfd5d3 55%,#3aa6de 78%,#b59c82)" role="img" aria-label="Modern house with covered patio and pool"></div>
  <div class="btn" style="left:515px;top:2870px;width:171px;height:39px">View More</div>
</section>

<svg class="abs" style="left:0;top:2955px" width="1200" height="90" viewBox="0 0 1200 90" preserveAspectRatio="none">
  <path d="M0 30 C160 10 300 45 480 28 S780 5 960 25 S1120 38 1200 20 V90 H0Z" fill="var(--blue)"/>
</svg>
<footer class="abs" style="left:0;top:3020px;width:1200px;height:274px;background:var(--blue)">
</footer>
<div class="photo" style="left:141px;top:3029px;width:248px;height:248px;border-radius:50%;background:linear-gradient(160deg,#2f8fe0,#1450b0)" role="img" aria-label="Person cleaning a pool with a long pole, seen from above"></div>
<nav class="abs footer-nav"><span>Home</span><span>About Us</span><span>Serivces</span><span>News</span><span>Contact Us</span></nav>
<div class="abs footer-rule"></div>
<p class="abs copyright">Copyright ©2024 Marlow Pool Service.&nbsp; All rights reserved&nbsp; |&nbsp; Privacy Policy&nbsp; |&nbsp; Terms of Use</p>
<div class="abs social" aria-label="Social links"><span></span><span></span><span></span></div>

</body>
</html>
```